Label Design for Climbing Chalk (fitness category)

I am looking for someone to design a front and back label for a bottle of liquid chalk. Liquid chalk is used in gyms, gymnastics, climbing to prevent your hands from getting moist and increase friction. I'm uploading some design motivations that I like.

The bottle is going to be black and I want the label to be clear. You have free reign of how you want to approach this design. Below are more specifics for the sizing:

*Attached is a picture of a competitor product (Tor Hold Liquid Chalk). Please don't use this for motivation, their label is very bad. I'm attaching a picture so that you can see what the bottle looks like.
*Attached are design motivations that I like
*The bottle is 50 ml, it's 3.75 inches tall, 2 inches wide and 1.25 inches in depth.
*The label can be square or oval (it's up to you). The size of the label needs to be 1,25 x 2.25 inches.
*Name of the product: Bravan Liquid Chalk
*Label needs to have the following Required Text. You can arrange it however you like:
- (50 ml)
- Made by USA Competitive Athletes for Athletes. Increases grip and lasts 3-4 times longer than regular chalk.
- Directions: Shake well. Squeeze some Bravan Liquid Chalk into your hand and rub your hands together. Let your hands air dry for about 10 seconds. To remove the chalk wash your hands with light soap.
Warning: Avoid contact with Eyes. Do not use on broken skin. Do not ingest. Keep out of reach of small children.
- Ingredients: Magnesium carbonate, SD Alcohol, hydroxypropylcellulose, colophonium.

Target Market(s)

Fitness, Athletes, Rock Climbers, Weight Lifters, Gymnasts, etc

Industry/Entity Type

Fitness

Font styles to use
Sans Serif

Colors

Designer to choose colors to be used in the design.

Requirements
Must have
• Please see Project Description for required text. The bottle is going to be black and I want the clear label so please be creative with the colors that would look good
Nice to have
• Please see attached branding ideas that I liked for font and colors. You don't have to strictly stick to them, these are just some of the ones I liked. Be creative and put your best foot forward.

```html
<!DOCTYPE html>
<html lang="en">
<head>
<meta charset="utf-8">
<title>Bravan Liquid Chalk – Front and Back Labels</title>
<link rel="stylesheet" href="https://fonts.googleapis.com/css2?family=Anton&family=Overpass:ital,wght@0,400;0,500;1,400;1,500;1,700;1,800;1,900&display=swap">
<style>
  :root {
    --page: #ffffff;
    --label: #0b0b0b;
    --rim: #ffffff;
    --brand-red: #c1272d;
    --text: #ffffff;
    --texture-light: #8c8c8c;
    --texture-dark: #1a1a1a;
    --shadow: rgba(0, 0, 0, 0.45);
  }
  * { margin: 0; padding: 0; box-sizing: border-box; }
  html, body {
    width: 1200px; height: 1029px; overflow: hidden;
    background: var(--page);
  }
  .canvas { position: relative; width: 1200px; height: 1029px; }

  .label {
    position: absolute; top: 132px;
    width: 432px; height: 780px;
    border-radius: 216px;
    background: var(--label);
    border: 6px solid var(--rim);
    box-shadow: 10px 22px 28px var(--shadow);
    overflow: hidden;
    color: var(--text);
    font-family: "Overpass", sans-serif;
  }
  .label--front { left: 134px; }
  .label--back { left: 650px; }

  .chalk-texture {
    position: absolute; left: 60px; top: 0; width: 300px; height: 100%;
    background: radial-gradient(ellipse 45% 50% at 55% 50%, var(--texture-light) 0%, rgba(90,90,90,0.55) 45%, var(--texture-dark) 85%, transparent 100%);
    opacity: 0.75;
  }

  .brand-name {
    position: absolute; left: 0; width: 100%;
    text-align: center;
    font-family: "Overpass", sans-serif;
    font-weight: 800; font-style: normal;
    color: var(--brand-red);
    letter-spacing: 0.5px;
  }
  .label--front .brand-name { top: 88px; font-size: 66px; }
  .label--back .brand-name { top: 62px; font-size: 50px; }

  .product-title-vertical {
    position: absolute; left: 212px; top: 384px;
    transform: translate(-50%, -50%) rotate(90deg);
    font-family: "Anton", sans-serif;
    font-size: 118px; line-height: 132px;
    color: var(--text);
    text-transform: uppercase;
    text-align: left;
    white-space: nowrap;
    font-style: italic;
    -webkit-text-stroke: 3px #000;
    paint-order: stroke fill;
    text-shadow: 4px 4px 0 #000;
  }

  .front-claim {
    position: absolute; left: 0; width: 100%; top: 574px;
    text-align: center;
    font-style: italic; font-size: 19px; line-height: 21px;
    letter-spacing: 0.8px;
    text-shadow: 0 0 4px #000, 0 0 8px #000;
  }
  .volume {
    position: absolute; left: 0; width: 100%; top: 708px;
    text-align: center; font-size: 29px; font-style: italic; letter-spacing: 1px;
  }

  .back-title {
    position: absolute; left: 0; width: 100%; top: 144px;
    text-align: center;
    font-weight: 900; font-style: italic; font-size: 32px;
    letter-spacing: -0.5px; text-transform: uppercase;
  }
  .info-heading {
    position: absolute; left: 48px;
    color: var(--brand-red);
    font-weight: 700; font-style: italic; font-size: 22px; letter-spacing: 0.5px;
  }
  .info-body {
    position: absolute; left: 48px; width: 360px;
    font-size: 18px; line-height: 24px; letter-spacing: 1.1px; font-weight: 500;
  }
  .directions-heading { top: 244px; }
  .directions-body { top: 269px; }
  .warning-heading { top: 430px; }
  .warning-body { top: 456px; }
  .divider {
    position: absolute; left: 82px; top: 548px;
    width: 274px; height: 7px; background: var(--text);
  }
  .ingredients-heading {
    position: absolute; left: 0; width: 100%; top: 584px;
    text-align: center; font-weight: 800; font-style: italic; font-size: 20px; letter-spacing: 0.5px;
  }
  .ingredients-list {
    position: absolute; left: 0; width: 100%; top: 610px;
    text-align: center; font-style: italic; font-size: 18px; line-height: 24px; letter-spacing: 0.8px;
  }
</style>
</head>
<body>
<main class="canvas">

  <section class="label label--front" aria-label="Front label">
    <div class="chalk-texture" role="img" aria-label="Grey chalk powder texture running down the label"></div>
    <div class="brand-name">Bravan</div>
    <h1 class="product-title-vertical">Liquid<br>Chalk</h1>
    <p class="front-claim">Made by USA Competitive<br>Athletes for Athletes.<br>Increases grip and lasts<br>4-3 times longer than<br>regular chalk.</p>
    <p class="volume">50 ml</p>
  </section>

  <section class="label label--back" aria-label="Back label">
    <div class="brand-name">Bravan</div>
    <h2 class="back-title">Liquid Chalk</h2>

    <h3 class="info-heading directions-heading">Directions:</h3>
    <p class="info-body directions-body">Shake well. Squeeze some Bravan<br>Liquid Chalk into your hand and rub<br>your hands together. Let your hands<br>air dry for about 10 seconds. To<br>remove the chalk wash your hands<br>with light soap.</p>

    <h3 class="info-heading warning-heading">Warning:</h3>
    <p class="info-body warning-body">Avoid contact with Eyes. Do not use<br>on broken skin. Do not ingest. Keep<br>out of reach of small children.</p>

    <div class="divider"></div>

    <h3 class="ingredients-heading">Ingredients:</h3>
    <p class="ingredients-list">Magnesium carbonate, SD Alcohol,<br>hydroxypropylcellulose,<br>colophonium.</p>
  </section>

</main>
</body>
</html>
```